Redesign of business card for Cedar Ridge Mechanical

We are looking for a new design for our business cards for Cedar Ridge Mechanical. We are a plumbing & HVAC construction company, operating on the West Coast of Canada and USA. Logo attached.
Industry/Entity Type
Construction - Plumbing & HVAC
Contact Information for Business Card
Name, address, phone numbers, email, website address
Look and feel
Each slider illustrates characteristics of the customer's brand and the style your logo design should communicate.

```html
<!DOCTYPE html>
<html lang="en">
<head>
<meta charset="UTF-8">
<title>Cedar Ridge Mechanical – Business Card</title>
<link rel="stylesheet" href="https://fonts.googleapis.com/css2?family=Oswald:wght@500&family=Montserrat:wght@400;700&display=swap">
<style>
  :root {
    --backdrop: #7a6650;
    --card-light: #ffffff;
    --card-dark: #262626;
    --ink: #1f1f1f;
    --ink-soft: #2a2a2a;
    --paper: #ffffff;
  }
  html, body {
    margin: 0;
    padding: 0;
    width: 900px;
    height: 1200px;
    overflow: hidden;
    background: var(--backdrop);
  }
  .canvas {
    position: relative;
    width: 900px;
    height: 1200px;
  }
  .card {
    position: absolute;
    border-radius: 22px;
    box-shadow: 0 6px 14px rgba(0,0,0,0.35);
  }
  .card--front {
    left: 80px; top: 130px;
    width: 742px; height: 442px;
    background: var(--card-light);
    color: var(--ink);
  }
  .card--back {
    left: 78px; top: 640px;
    width: 744px; height: 438px;
    background: var(--card-dark);
    color: var(--paper);
  }
  .company-heading {
    position: absolute;
    left: 24px; top: 56px;
    margin: 0;
    font-family: "Oswald", sans-serif;
    font-weight: 500;
    font-size: 37px;
    letter-spacing: 1.5px;
    line-height: 1;
    transform: scaleX(0.86);
    transform-origin: left center;
  }
  .person {
    position: absolute;
    left: 35px; top: 150px;
    font-family: "Montserrat", sans-serif;
  }
  .person__name {
    margin: 0;
    font-weight: 700;
    font-size: 25px;
    line-height: 1.1;
  }
  .person__title {
    margin: 4px 0 0;
    font-size: 15.5px;
  }
  .address {
    position: absolute;
    left: 35px; top: 236px;
    margin: 0;
    font-family: "Montserrat", sans-serif;
    font-style: normal;
    font-size: 16px;
    line-height: 20px;
  }
  .contacts {
    position: absolute;
    left: 37px; top: 317px;
    margin: 0; padding: 0;
    list-style: none;
    font-family: "Montserrat", sans-serif;
    font-size: 15.5px;
  }
  .contacts li {
    display: flex;
    align-items: center;
    height: 30px;
  }
  .contacts svg {
    width: 15px; height: 15px;
    margin-right: 12px;
    fill: var(--ink-soft);
  }
  .brand-mark {
    position: absolute;
    left: 322px; top: 138px;
    width: 362px; height: 234px;
    display: flex;
    flex-direction: column;
    align-items: center;
    justify-content: center;
    gap: 14px;
    font-family: "Oswald", sans-serif;
    font-weight: 500;
    color: var(--ink);
    text-align: center;
  }
  .brand-mark__square {
    width: 38px; height: 38px;
    background: currentColor;
  }
  .brand-mark__name {
    font-size: 42px;
    line-height: 1.05;
    letter-spacing: 1.5px;
    text-transform: uppercase;
  }
  .brand-mark--reverse {
    left: 0; top: 0;
    width: 744px; height: 438px;
    color: var(--paper);
  }
  .brand-mark--reverse .brand-mark__name {
    font-size: 46px;
  }
</style>
</head>
<body>
<main class="canvas">
  <section class="card card--front" aria-label="Business card front">
    <h1 class="company-heading">CEDAR RIDGE MECHANICAL</h1>
    <div class="person">
      <p class="person__name">Daniel Moreau</p>
      <p class="person__title">Managing Director</p>
    </div>
    <address class="address">245 Harbor View Road<br>Camden, MS 39045</address>
    <ul class="contacts">
      <li>
        <svg viewBox="0 0 24 24" aria-hidden="true"><path d="M6.6 10.8c1.4 2.8 3.8 5.1 6.6 6.6l2.2-2.2c.3-.3.7-.4 1-.2 1.1.4 2.3.6 3.6.6.6 0 1 .4 1 1V20c0 .6-.4 1-1 1C10.6 21 3 13.4 3 4c0-.6.4-1 1-1h3.5c.6 0 1 .4 1 1 0 1.3.2 2.5.6 3.6.1.3 0 .7-.2 1L6.6 10.8z"/></svg>
        <span>888.555.0142</span>
      </li>
      <li>
        <svg viewBox="0 0 24 24" aria-hidden="true"><path d="M2 5h20v2l-10 6L2 7V5zm0 4l10 6 10-6v10H2V9z"/></svg>
        <span>info@cedarridgemechanical.com</span>
      </li>
      <li>
        <svg viewBox="0 0 24 24" aria-hidden="true"><path d="M12 2a10 10 0 1 0 0 20 10 10 0 0 0 0-20zm-1 17.9A8 8 0 0 1 4.1 11H7c.1 3.2 1.5 6.3 4 8.9zm0-10.9H7.1C7.4 6.6 8.6 4.6 11 4.1V9zm2-4.9c2.4.5 3.6 2.5 3.9 4.9H13V4.1zm0 6.9h4c-.1 3-1.4 5.8-4 8.1V11zm2.6 8.4c1.9-2.4 2.9-5.3 3-8.4h2.3a8 8 0 0 1-5.3 8.4z"/></svg>
        <span>www.cedarridgemechanical.com</span>
      </li>
    </ul>
    <div class="brand-mark">
      <span class="brand-mark__square" aria-hidden="true"></span>
      <span class="brand-mark__name">Cedar Ridge<br>Mechanical</span>
    </div>
  </section>

  <section class="card card--back" aria-label="Business card back">
    <div class="brand-mark brand-mark--reverse">
      <span class="brand-mark__square" aria-hidden="true"></span>
      <span class="brand-mark__name">Cedar Ridge Mechanical</span>
    </div>
  </section>
</main>
</body>
</html>
```